Zielgruppe
Ich biete Farbtupferei, Glitzertattoos, Schwangerschaftsbemalung (Belly-Painting), Wunden schminken, Vermietung von einer Popcornmaschine.
Aufgabenstellung
Mein Anliegen betrifft hiermit die Gestaltung einer Website.
In Bezug auf die Website gibt es schon eine gekaufte Domain, welche lautet: frau-pinselmaus.de und kann über VERAX eingerichtet werden.
Auf dieser WEBSITE soll sich folgendes Menü befinden:
- Anfrage stellen/Angebot einholen mit zusätzlicher Frage 'Wie sind Sie auf mich aufmerksam geworden?'
Mit einem Feld für den Namen, E-Mail, Telefonnummer, Gewünschtes Datum.
Sowie die Frage 'Wie sind Sie auf mich aufmerksam geworden?' (zum Ankreuzen) Freunde, Empfehlung, Flyer, soziale medienoder sonstiges.
Gerne auch zum ankreuzen welche Leistung Sie möchten. Farbtupferei, Glitzer Tattoos, Schwangerschaftsbemalung, oder Popcornmaschiene. (So brauchen haben es die Kunden einfacher nur anzukreuzen und ich sehe gleich worum es sich handelt.)
- eine Leistungsübersicht: Farbtupferei, Glitzertattoos, Schwangerschaftsbemalung (Belly-Painting), Wunden schminken, Vermietung von einer Popcornmaschine
- meine Kontaktdaten
- Galerie (es kann eine Auswahl der angehängten Bilder sein)
!!! mein Wunsch wäre, dass sich die Figur von dem Logo in verschiedenen Positionen auf der Website an das Menü angepasst wiederfindet (wenn dies irgendwie machbar ist)
z.B. meine Figur (Logo) stehend am Rand oder liegend.....
- erwünscht ist auch eine Verknüpfung mit einem Findlaeintrag
- Hinweis auf Kontaktor und Lumoravue (bin gerade dabei ein öffentliches Profil dort zu erstellen)
!Wichtig wäre die nötige Einstellung, damit die Website sowohl in der mobilen Version als auch der PC-Version mit ALLEN oben genannten Informationen dargestellt wird!
Dankbar wäre ich noch für die Information, ob für mich laufende Kosten (monatlich oder jährlich) für die Website entstehen?
Mein Logo ist mir sehr wichtig und sollte gut sichtbar und erkennbar sein auch die Schriftart kann auf der Website aufgegriffen werden

```html
<!DOCTYPE html>
<html lang="de">
<head>
<meta charset="utf-8">
<title>Frau Pinselmaus – Farbtupferei & Glitzertattoos</title>
<link href="https://fonts.googleapis.com/css2?family=Hind:wght@600;700&family=Poppins:wght@300;400;500;600&display=swap" rel="stylesheet">
<style>
:root{
  --teal:#1a9aae;
  --teal-deep:#2aa6b5;
  --mist:#e6f4f6;
  --ink:#111;
  --white:#fff;
  --orange:#f47e3e;
}
*{box-sizing:border-box;margin:0;padding:0}
html,body{width:1200px;height:4405px;overflow:hidden}
body{
  position:relative;
  font-family:"Poppins",sans-serif;
  color:var(--ink);
  background:linear-gradient(180deg,var(--white) 0px,var(--mist) 1600px,#b9e2e7 2500px,#6fc3cd 3200px,var(--teal-deep) 4128px,var(--white) 4128px);
}
.abs{position:absolute}
.brand{display:flex;align-items:center;gap:12px;font-weight:500;color:var(--teal);font-size:30px;line-height:1.1;white-space:nowrap}
.brand-dot{width:26px;height:26px;border-radius:50%;background:var(--teal);flex:none}
.nav a{position:absolute;top:80px;font-size:22px;color:var(--teal);text-decoration:none;font-weight:400;letter-spacing:.5px}
.nav a.active{font-weight:600}
.section-title{font-family:"Hind",sans-serif;font-weight:700;font-size:96px;line-height:1;letter-spacing:0;white-space:nowrap}
.title-teal{color:var(--teal)}
.title-white{color:var(--white)}
.service-label{font-weight:600;font-size:38px;line-height:1;white-space:nowrap}
.photo{position:absolute}
.tone-skin{background:linear-gradient(135deg,#d8b49f,#8f6a5a)}
.tone-dark{background:linear-gradient(135deg,#4a4440,#1f1c1a)}
.tone-green{background:linear-gradient(135deg,#5d7a43,#2b3a22)}
.tone-red{background:linear-gradient(135deg,#e0c4b6,#8a2f2c)}
.tone-pink{background:linear-gradient(135deg,#d6a9b4,#a77a86)}
.tone-blue{background:linear-gradient(135deg,#3f86b8,#8a5a3b)}
.tone-pop{background:linear-gradient(135deg,#d9c8c2,#b83b36)}
.review{position:absolute;border:3px solid var(--orange);border-radius:4px;display:flex;flex-direction:column;align-items:center;justify-content:center;text-align:center;padding:10px 24px;font-size:19px;line-height:1.45}
.stars{color:var(--white);font-size:20px;letter-spacing:2px;margin-bottom:14px}
.palette{position:absolute;border-radius:50%;background:var(--white);border:4px solid var(--ink)}
.field{position:absolute;left:256px;width:711px;border:2px solid var(--white);color:var(--white);font-size:28px;padding:0 8px;display:flex;align-items:center}
.form-text{position:absolute;color:var(--white);font-size:28px;white-space:nowrap}
.check{display:flex;align-items:center;gap:14px;position:absolute;color:var(--white);font-size:29px;white-space:nowrap}
.check .box{width:37px;height:37px;border:2px solid var(--white);border-radius:4px}
.submit{position:absolute;left:256px;top:4003px;width:711px;height:51px;background:var(--orange);color:var(--white);font-size:28px;display:flex;align-items:center;justify-content:center}
.contact{position:absolute;right:19px;top:4172px;text-align:right;color:var(--teal);font-size:29px;line-height:42px;font-style:normal}
.social{position:absolute;right:19px;top:4330px;display:flex;gap:18px;color:var(--teal);font-size:20px}
.social span{display:flex;align-items:center;gap:6px}
.social i{width:16px;height:16px;background:var(--teal);display:inline-block}
</style>
</head>
<body>

<header>
  <div class="brand abs" style="left:26px;top:76px"><span class="brand-dot"></span>Frau Pinselmaus</div>
  <nav class="nav">
    <a style="left:325px" href="#leistungen">LEISTUNGEN</a>
    <a style="left:574px" href="#galerie">GALERIE</a>
    <a style="left:781px" href="#referenzen">REFERENZEN</a>
    <a class="active" style="left:1031px" href="#kontakt">KONTAKT</a>
  </nav>
</header>

<section id="leistungen">
  <h2 class="section-title title-teal abs" style="left:20px;top:248px">LEISTUNGEN</h2>

  <div class="service-label abs" style="left:0;top:440px">Belly Painting</div>
  <div class="photo tone-dark" style="left:20px;top:489px;width:214px;height:190px" role="img" aria-label="Foto einer Schwangerschaftsbemalung"></div>

  <div class="photo tone-skin" style="left:251px;top:526px;width:209px;height:175px" role="img" aria-label="Foto von Glitzertattoos am Handgelenk"></div>
  <div class="service-label abs" style="left:350px;top:712px;transform:translateX(-50%)">Glitzertattoos</div>

  <div class="service-label abs" style="left:593px;top:440px;transform:translateX(-50%)">Farbtupferei</div>
  <div class="photo tone-dark" style="left:484px;top:485px;width:206px;height:175px" role="img" aria-label="Foto beim Gesichtsschminken"></div>

  <div class="photo tone-pop" style="left:709px;top:526px;width:198px;height:175px" role="img" aria-label="Foto einer Popcornmaschine mit Spielzeugauto"></div>
  <div class="service-label abs" style="left:803px;top:712px;transform:translateX(-50%)">Verleih</div>
  <div class="service-label abs" style="left:808px;top:767px;transform:translateX(-50%)">Popcornmaschine</div>

  <div class="service-label abs" style="left:1046px;top:368px;transform:translateX(-50%)">Wunden</div>
  <div class="service-label abs" style="left:1048px;top:425px;transform:translateX(-50%)">Schminken</div>
  <div class="photo tone-red" style="left:942px;top:485px;width:210px;height:182px" role="img" aria-label="Foto einer geschminkten Wunde"></div>
</section>

<section id="galerie">
  <h2 class="section-title title-teal abs" style="right:48px;top:842px">GALERIE</h2>
  <div class="photo tone-green" style="left:44px;top:954px;width:371px;height:316px" role="img" aria-label="Galeriefoto: Bauchbemalung im Grünen"></div>
  <div class="photo tone-pink" style="left:417px;top:954px;width:367px;height:316px" role="img" aria-label="Galeriefoto: Glitzertattoo wird aufgetragen"></div>
  <div class="photo tone-blue" style="left:790px;top:954px;width:365px;height:316px" role="img" aria-label="Galeriefoto: Körperbemalung in Blau"></div>
  <div class="photo tone-green" style="left:44px;top:1275px;width:371px;height:332px" role="img" aria-label="Galeriefoto: Gruppe mit Bemalungen"></div>
  <div class="photo tone-pink" style="left:417px;top:1275px;width:367px;height:332px" role="img" aria-label="Galeriefoto: Glitzer auf dem Arm"></div>
  <div class="photo tone-dark" style="left:790px;top:1275px;width:365px;height:332px" role="img" aria-label="Galeriefoto: bemalte Hand"></div>
  <div class="photo tone-dark" style="left:50px;top:1610px;width:365px;height:333px" role="img" aria-label="Galeriefoto: Gesichtsbemalung"></div>
  <div class="photo tone-blue" style="left:417px;top:1610px;width:367px;height:333px" role="img" aria-label="Galeriefoto: Rückenbemalung"></div>
</section>

<section id="referenzen">
  <h2 class="section-title title-white abs" style="left:585px;top:2072px;transform:translateX(-50%)">REFERENZEN</h2>
  <div class="review" style="left:87px;top:2206px;width:492px;height:113px"><div class="stars">★★★★★</div>Alles Bestens, würde ich wieder buchen!</div>
  <div class="review" style="left:612px;top:2206px;width:492px;height:113px"><div class="stars">★★★★★</div>Ich kann nichts sagen außer, super!</div>
  <div class="review" style="left:87px;top:2334px;width:489px;height:201px"><div class="stars">★★★★★</div>So freundlich zu den kleinen. Habe Sie zu einem Kindergeburtstag meiner Tochter gebucht und diese war begesitert. Wirklich zu empfehlen.</div>
  <div class="review" style="left:612px;top:2334px;width:487px;height:201px"><div class="stars">★★★★★</div>Die Kids sind super auf die Popcornmaschine abgefahren.<br>War der Hit der Feier!</div>
  <div class="palette" style="left:1051px;top:2157px;width:94px;height:94px" role="img" aria-label="Malpaletten-Illustration"></div>
  <div class="palette" style="left:51px;top:2483px;width:94px;height:94px" role="img" aria-label="Malpaletten-Illustration"></div>
</section>

<section id="kontakt">
  <h2 class="section-title title-white abs" style="left:612px;top:2627px;transform:translateX(-50%)">INTERESSE GEWECKT?</h2>
  <h2 class="section-title title-white abs" style="left:612px;top:2765px;transform:translateX(-50%)">KONTAKT</h2>

  <div class="field" style="top:2916px;height:51px">Name</div>
  <div class="field" style="top:2989px;height:51px">E-Mail Adresse</div>
  <div class="field" style="top:3073px;height:51px">Gewünschtes Datum</div>

  <div class="form-text" style="left:264px;top:3150px">Welche Leistung wollen Sie in Anspruch nehmen?</div>
  <div class="check" style="left:256px;top:3202px"><span class="box"></span>Farbtupferei</div>
  <div class="check" style="left:256px;top:3252px"><span class="box"></span>Glitzertattoos</div>
  <div class="check" style="left:256px;top:3307px"><span class="box"></span>Popcornmaschine mieten</div>
  <div class="check" style="left:256px;top:3365px"><span class="box"></span>Sonstiges</div>

  <div class="form-text" style="left:264px;top:3419px">Wie sind Sie auf mich aufmerksam geworden?</div>
  <div class="check" style="left:256px;top:3471px"><span class="box"></span>Freunde</div>
  <div class="check" style="left:458px;top:3471px"><span class="box"></span>Sozial Media</div>
  <div class="check" style="left:711px;top:3471px"><span class="box"></span>Empfehlung</div>
  <div class="check" style="left:256px;top:3529px"><span class="box"></span>Sonstiges</div>

  <div class="field" style="top:3609px;height:359px;align-items:flex-start;padding-top:4px">Ihre Nachricht</div>
  <div class="submit">Absenden</div>
</section>

<footer>
  <div class="brand abs" style="left:38px;top:4245px"><span class="brand-dot"></span>Frau Pinselmaus</div>
  <address class="contact">
    Lena Beispiel<br>
    Telefon: 0431 87265390<br>
    Email: hallo@pinsel.de
  </address>
  <div class="social"><span><i></i>Kontaktor</span><span><i></i>Lumoravue</span></div>
</footer>

</body>
</html>
```